Marlow Sail Works President Business Card Carbon fiber catamarans

Hi.. I need a new business card design.. I am the President of a high tech yacht builder. We build Carbon Fiber go fast catamarans... Maybe we use the file I am sharing to you as the back of the card.. We need to look cool and crisp ...

Target Market(s)

Affluent People who will purchase a cool yacht

Industry/Entity Type

Custom Yacht Builder

Contact Information for Business Card

Dean Pellway , President, 731.508.2164 USA

Font styles to use
Serif

Requirements
Must have
• the clean crisp cool feel
Nice to have
• clean and crisp
Should not have
• Bold ugly

```html
<!DOCTYPE html>
<html lang="en">
<head>
<meta charset="utf-8">
<title>Marlow Sail Works – President Business Card</title>
<link rel="stylesheet" href="https://fonts.googleapis.com/css2?family=Arimo:wght@400;700&display=swap">
<style>
  :root {
    --backdrop: #121213;
    --card: #2b2b2d;
    --card-edge: #4a4a4d;
    --ink: #f2f2f2;
    --ink-soft: #d4d4d6;
    --rule: #bdbdbf;
    --emboss: #202022;
    --emboss-light: #3a3a3d;
  }
  * { box-sizing: border-box; margin: 0; padding: 0; }
  html, body {
    width: 1200px;
    height: 963px;
    overflow: hidden;
    background: var(--backdrop);
    font-family: "Arimo", Arial, sans-serif;
    color: var(--ink);
  }
  .sheet {
    width: 1200px;
    height: 963px;
    display: flex;
    flex-direction: column;
    align-items: center;
    justify-content: center;
    gap: 40px;
  }
  .card {
    position: relative;
    width: 700px;
    height: 400px;
    background: var(--card);
    border-radius: 22px;
    box-shadow: 0 0 0 1px var(--card-edge), 0 18px 40px rgba(0,0,0,.55);
  }

  /* Front */
  .card-front .brand {
    position: absolute;
    left: 60px;
    top: 120px;
    width: 270px;
  }
  .brand-name {
    font-size: 34px;
    font-weight: 400;
    letter-spacing: 5px;
    line-height: 1.15;
    text-transform: uppercase;
    color: var(--ink);
  }
  .divider {
    position: absolute;
    left: 360px;
    top: 140px;
    width: 1px;
    height: 200px;
    background: var(--rule);
  }
  .details {
    position: absolute;
    left: 392px;
    top: 150px;
    width: 280px;
  }
  .person-name {
    font-size: 24px;
    font-weight: 700;
    letter-spacing: .5px;
    text-transform: uppercase;
  }
  .person-title {
    font-size: 17px;
    color: var(--ink-soft);
    margin-top: 2px;
  }
  .address {
    font-size: 17px;
    line-height: 1.25;
    color: var(--ink-soft);
    margin-top: 14px;
  }
  .contact-list {
    list-style: none;
    margin-top: 10px;
  }
  .contact-list li {
    display: flex;
    align-items: center;
    gap: 10px;
    font-size: 17px;
    line-height: 1.5;
  }
  .contact-list svg { width: 15px; height: 15px; flex: none; }

  /* Back */
  .card-back {
    display: flex;
    align-items: center;
    justify-content: center;
  }
  .card-back .brand-name {
    font-size: 48px;
    letter-spacing: 9px;
    text-align: center;
    color: var(--emboss);
    text-shadow: 0 1px 0 var(--emboss-light);
  }
</style>
</head>
<body>
<main class="sheet">
  <section class="card card-front" aria-label="Card front">
    <div class="brand">
      <p class="brand-name">Marlow Sail Works</p>
    </div>
    <div class="divider"></div>
    <div class="details">
      <p class="person-name">Dean Pellway</p>
      <p class="person-title">President</p>
      <p class="address">Your address, city<br>state, ZIP 0000</p>
      <ul class="contact-list">
        <li>
          <svg viewBox="0 0 16 16" aria-hidden="true"><path fill="#f2f2f2" d="M3.6 1.5l2.3 2.6-1.4 1.7c.9 2 2.5 3.6 4.5 4.6l1.7-1.4 2.6 2.3-1.3 2.2C6.4 13.3 2.7 9.6 1.5 2.8z"/></svg>
          731.508.2164
        </li>
        <li>
          <svg viewBox="0 0 16 16" aria-hidden="true"><rect x="1" y="3" width="14" height="10" rx="1" fill="#f2f2f2"/><path d="M1.5 3.8L8 9l6.5-5.2" fill="none" stroke="#2b2b2d" stroke-width="1.3"/></svg>
          youremail@mailbox.com
        </li>
        <li>
          <svg viewBox="0 0 16 16" aria-hidden="true"><circle cx="8" cy="8" r="6.5" fill="none" stroke="#f2f2f2" stroke-width="1.4"/><ellipse cx="8" cy="8" rx="2.8" ry="6.5" fill="none" stroke="#f2f2f2" stroke-width="1.2"/><path d="M1.5 8h13" stroke="#f2f2f2" stroke-width="1.2"/></svg>
          www.yourwebsite.com
        </li>
      </ul>
    </div>
  </section>

  <section class="card card-back" aria-label="Card back">
    <p class="brand-name">Marlow<br>Sail Works</p>
  </section>
</main>
</body>
</html>
```